Dental office stationary (letterhead, envelopes), business cards, presentation folders

Nothing too dental outside of the logo. I will need all stationary, presentation folders, business cards. Would prefer to stay in the colors of the logo

Gordon Patel, DDS
Bright Haven Dental Implant Center
555-318-2790
info@brighthavendental.example
4817 NW Maple Crest Rd Unit B
Lakeview, ST 00000

Also need appointment date and time
And cancellation policy
I want it to say “kindly ask for
A 48hr cancellation policy to avoid incurring a cancellation fee”

Industry/Entity Type

Dental

Colors
0054AA
0677BA
7BADD7
CADEEF
E8F1F8

Requirements
Must have
• Name of your office, name of doctor, address, phone number
Should not have
• Too much tooth/dental. Only the tooth in logo

```html
<!DOCTYPE html>
<html lang="en">
<head>
<meta charset="utf-8">
<title>Bright Haven Dental Implant Center – Business Card</title>
<link href="https://fonts.googleapis.com/css2?family=Roboto:ital,wght@0,400;0,500;0,700;1,400;1,700&display=swap" rel="stylesheet">
<style>
  :root {
    --blue-deep: #0d6bbd;
    --blue-bright: #14a9e0;
    --teal: #17b594;
    --brand-blue: #0677ba;
    --mist: #e8f5fa;
    --paper: #ffffff;
    --backdrop: #e4e7eb;
    --shadow: rgba(20, 40, 70, 0.18);
  }
  * { box-sizing: border-box; margin: 0; padding: 0; }
  html, body { width: 1200px; height: 900px; overflow: hidden; }
  body {
    background: var(--backdrop);
    font-family: "Roboto", Arial, sans-serif;
    display: flex;
    flex-direction: column;
    align-items: center;
    justify-content: center;
    gap: 40px;
  }
  .card {
    position: relative;
    width: 700px;
    height: 400px;
    background: var(--paper);
    box-shadow: 0 8px 24px var(--shadow);
    overflow: hidden;
  }
  .card-front__art { position: absolute; inset: 0; }
  .contact {
    position: absolute;
    left: 44px;
    top: 46px;
    color: var(--paper);
  }
  .contact__name { font-size: 25px; font-weight: 700; font-style: italic; }
  .contact__office { font-size: 17px; font-style: italic; margin-top: 4px; }
  .contact__address { font-size: 17px; font-style: italic; margin-top: 26px; line-height: 1.35; }
  .contact__lines { list-style: none; margin-top: 26px; font-size: 16px; font-style: italic; }
  .contact__lines li { display: flex; align-items: center; gap: 10px; line-height: 1.6; }
  .contact__lines svg { width: 16px; height: 16px; flex: none; }
  .brand {
    position: absolute;
    text-align: center;
    color: var(--brand-blue);
    font-weight: 500;
    text-transform: uppercase;
  }
  .brand__name { display: block; letter-spacing: 0.04em; }
  .brand__tag { display: block; letter-spacing: 0.3em; }
  .card-front .brand { left: 360px; top: 160px; width: 320px; }
  .card-front .brand__name { font-size: 38px; }
  .card-front .brand__tag { font-size: 12px; margin-top: 6px; }
  .card-back .brand { left: 0; right: 0; top: 150px; }
  .card-back .brand__name { font-size: 64px; }
  .card-back .brand__tag { font-size: 17px; margin-top: 10px; }
</style>
</head>
<body>

<section class="card card-front" aria-label="Business card front">
  <svg class="card-front__art" viewBox="0 0 700 400" aria-hidden="true">
    <defs>
      <linearGradient id="panelFill" x1="0" y1="0" x2="0.3" y2="1">
        <stop offset="0" stop-color="var(--blue-bright)"/>
        <stop offset="1" stop-color="var(--blue-deep)"/>
      </linearGradient>
    </defs>
    <circle cx="520" cy="250" r="190" fill="var(--mist)"/>
    <path d="M0 0 H470 C360 30 300 190 318 400 H0 Z" fill="url(#panelFill)"/>
    <path d="M478 0 C370 34 312 190 330 400" fill="none" stroke="var(--teal)" stroke-width="5"/>
  </svg>

  <div class="contact">
    <p class="contact__name">Gordon Patel, DDS</p>
    <p class="contact__office">Bright Haven Dental Implant Center</p>
    <p class="contact__address">4817 NW Maple Crest Rd Unit B<br>Lakeview, ST 00000</p>
    <ul class="contact__lines">
      <li>
        <svg viewBox="0 0 16 16" aria-hidden="true"><path fill="currentColor" d="M3 1.5l2.6 0 1.2 3-1.6 1.2a8 8 0 0 0 5.1 5.1l1.2-1.6 3 1.2v2.6c0 .8-.6 1.5-1.5 1.5C6.7 14.5 1.5 9.3 1.5 3 1.5 2.1 2.2 1.5 3 1.5z"/></svg>
        555-318-2790
      </li>
      <li>
        <svg viewBox="0 0 16 16" aria-hidden="true"><rect x="1" y="3" width="14" height="10" rx="1" fill="none" stroke="currentColor" stroke-width="1.5"/><path d="M1.5 3.8 8 9l6.5-5.2" fill="none" stroke="currentColor" stroke-width="1.5"/></svg>
        info@brighthavendental.example
      </li>
      <li>
        <svg viewBox="0 0 16 16" aria-hidden="true"><circle cx="8" cy="8" r="6.5" fill="none" stroke="currentColor" stroke-width="1.5"/><path d="M1.5 8h13M8 1.5c2.2 2 2.2 11 0 13M8 1.5c-2.2 2-2.2 11 0 13" fill="none" stroke="currentColor" stroke-width="1.2"/></svg>
        www.brighthavendental.example
      </li>
    </ul>
  </div>

  <p class="brand">
    <span class="brand__name">Bright Haven</span>
    <span class="brand__tag">Dental Implant Center</span>
  </p>
</section>

<section class="card card-back" aria-label="Business card back">
  <p class="brand">
    <span class="brand__name">Bright Haven</span>
    <span class="brand__tag">Dental Implant Center</span>
  </p>
</section>

</body>
</html>
```